Fitness Equipment & Service

I want to make the card eye catching and fun. We are called Corvane Motion Limited and we are based in Wales. We sell, install and service all types of fitness equipment from Skipping ropes, right through the Dumbbells, Kettle bells and Barbells through to state of the art Treadmills, Running Machines and Strength Equipment. We also design and install changing room furniture and lockers.

TYPOGRAPHY
We would like to use Futrura. Futura has an appearance of efficiency and forwardness. The typeface is derived
from simple geometric forms (near-perfect circles, triangles and squares) and is based on strokes of
near-even weight, which are low in contrast. This is most visible in the almost perfectly round stroke of
the o, which is nonetheless slightly ovoid.
The lowercase has tall ascenders, which rise above the cap line. The uppercase
characters present proportions similar to those of classical Roman capitals.

TYPOGRAPHIC CONSIDERATIONS
No Strike though
No Horizontal Scaling
No Drop Shadows
No Effects
Never use less than 120% Leading

OUR CORPORATE COLOURS
BRAND GUIDELINES
We were thinking that our primary colour palette consists of the Acid Green (Pantone 382) and Process Black.

We work closely with tquarly Ltd and would like to include their name on the card somewhere. I have attached images of the other brands that we work with as an idea or the small icons I have included that illustrate what we do?. I have very kindly been given permission to use any of the images off the files that I have included below, so I hope these help. I will include these below. I would be open to suggestions if it made the card more striking Can you do it?
Updates

Hi All, Just wanted to add a few thoughts but you are the guys with the creative visions (thats why are here) We are based in Wales, UK and we would be open to lots of different ideas on a theme but must be eye catching, Bold and FUN. If you can or think that the Welsh or any dragon could be put in there then go for it (its not a must have) We have also added some ideas for colour but again its over to you!! GO FOR IT ! Thanks and look forward to your visions! Owen

Hi All, Just thought I would sen through the contact details that need to be on the card. (if you want to play around with icons instead of the wording twitter, Facebook, go for it): Corvane Motion Limited Owen Pritchard Managing Director Mob: +44 (0)7582 913 406 e-mail: sales@corvanemotion.co.uk Web: Corvanemotion.co.uk twitter: @motionLetterbin Facebook: Corvane Motion Limited

```html
<!DOCTYPE html>
<html lang="en">
<head>
<meta charset="utf-8">
<title>Corvane Motion Limited – Business Card</title>
<link rel="stylesheet" href="https://fonts.googleapis.com/css2?family=Jost:wght@400;500;600;700&display=swap">
<style>
  :root {
    --backdrop: #8c8d8f;
    --card: #ececee;
    --navy: #1d2a5c;
    --gold: #a8893a;
    --ink: #1b1b1f;
    --body: #4a4a50;
    --rule: #c9c9cd;
    --tile-blue: #2f7fc0;
    --tile-light: #4ea6da;
    --tile-deep: #163a63;
    --tile-mid: #2a6e9d;
    --tile-grey: #6d889e;
    --tile-slate: #7c93a6;
    --scene-dark: #10213a;
    --scene-mid: #23466b;
    --white: #ffffff;
  }
  * { box-sizing: border-box; margin: 0; padding: 0; }
  html, body {
    width: 1105px; height: 1200px; overflow: hidden;
    background: var(--backdrop);
    font-family: "Jost", "Futura", sans-serif;
  }
  .card {
    position: absolute; left: 182px; width: 746px; height: 427px;
    background: var(--card); overflow: hidden;
  }
  .card--front { top: 119px; }
  .card--back { top: 637px; }

  /* Front */
  .brand-mark {
    position: absolute; left: 138px; top: 125px;
    width: 120px; height: 120px; border-radius: 50%;
    background: var(--navy);
  }
  .brand-name {
    position: absolute; left: 48px; top: 290px; width: 300px;
    text-align: center; font-size: 19px; font-weight: 500;
    color: var(--navy); line-height: 1.25;
  }
  .divider {
    position: absolute; left: 335px; top: 99px;
    width: 1px; height: 252px; background: var(--rule);
  }
  .contact { position: absolute; left: 375px; top: 104px; }
  .contact__name { font-size: 28px; font-weight: 500; color: var(--navy); line-height: 1.25; }
  .contact__role { font-size: 21px; color: var(--gold); line-height: 1.3; }
  .contact__address { margin-top: 26px; font-size: 20px; color: var(--body); line-height: 1.3; }
  .contact__list { list-style: none; margin-top: 14px; }
  .contact__item {
    display: flex; align-items: center; gap: 9px;
    font-size: 20px; color: var(--body); line-height: 1.42;
  }
  .contact__icon { width: 16px; height: 16px; fill: var(--navy); flex: none; }

  /* Back */
  .mosaic {
    position: absolute; left: 0; top: 0; width: 746px; height: 307px;
    background: linear-gradient(135deg, var(--scene-mid), var(--scene-dark) 70%);
  }
  .tile { position: absolute; width: 102px; height: 102px; }
  .tile--blue { background: var(--tile-blue); }
  .tile--light { background: var(--tile-light); }
  .tile--deep { background: var(--tile-deep); }
  .tile--mid { background: var(--tile-mid); }
  .tile--grey { background: var(--tile-grey); }
  .tile--slate { background: var(--tile-slate); }
  .partner {
    position: absolute; left: 306px; top: 118px; width: 306px;
    text-align: center; color: var(--white);
  }
  .partner__name { font-size: 44px; font-weight: 600; letter-spacing: 1px; line-height: 1.2; }
  .partner__tagline { font-size: 15px; font-weight: 600; letter-spacing: 0.5px; line-height: 1.3; }
  .social {
    position: absolute; left: 0; top: 330px; width: 746px;
    text-align: center; font-size: 26px; line-height: 1.28; color: var(--body);
  }
  .social__label { color: var(--ink); }
</style>
</head>
<body>

<section class="card card--front">
  <div class="brand-mark"></div>
  <div class="brand-name">Corvane Motion Limited</div>
  <div class="divider"></div>
  <div class="contact">
    <div class="contact__name">Owen Pritchard</div>
    <div class="contact__role">Managing Director</div>
    <div class="contact__address">42 Heron Quay Road<br>Cardiff, Wales CF10 7QX</div>
    <ul class="contact__list">
      <li class="contact__item">
        <svg class="contact__icon" viewBox="0 0 16 16"><path d="M4 0h8a1 1 0 0 1 1 1v14a1 1 0 0 1-1 1H4a1 1 0 0 1-1-1V1a1 1 0 0 1 1-1zm1 2v10h6V2zm3 11a1 1 0 1 0 0 2 1 1 0 0 0 0-2z"/></svg>
        +44 (0)7582 913 406
      </li>
      <li class="contact__item">
        <svg class="contact__icon" viewBox="0 0 16 16"><path d="M0 3h16v1.2L8 9 0 4.2zm0 2.6 8 4.8 8-4.8V13H0z"/></svg>
        sales@corvanemotion.co.uk
      </li>
      <li class="contact__item">
        <svg class="contact__icon" viewBox="0 0 16 16"><circle cx="8" cy="8" r="7.5"/><path d="M1 8h14M8 1c-3 3.5-3 10.5 0 14M8 1c3 3.5 3 10.5 0 14" stroke="#ececee" stroke-width="1" fill="none"/></svg>
        Corvanemotion.co.uk
      </li>
    </ul>
  </div>
</section>

<section class="card card--back">
  <div class="mosaic" role="img" aria-label="Gym interior with treadmills behind a grid of fitness equipment icon tiles">
    <div class="tile tile--blue" style="left:0;top:0"></div>
    <div class="tile tile--light" style="left:102px;top:0"></div>
    <div class="tile tile--deep" style="left:306px;top:0"></div>
    <div class="tile tile--blue" style="left:408px;top:0"></div>
    <div class="tile tile--mid" style="left:510px;top:0"></div>
    <div class="tile tile--slate" style="left:714px;top:0"></div>
    <div class="tile tile--grey" style="left:102px;top:102px"></div>
    <div class="tile tile--blue" style="left:204px;top:102px"></div>
    <div class="tile tile--deep" style="left:612px;top:102px"></div>
    <div class="tile tile--blue" style="left:714px;top:102px"></div>
    <div class="tile tile--mid" style="left:204px;top:204px"></div>
    <div class="tile tile--light" style="left:408px;top:204px"></div>
    <div class="tile tile--grey" style="left:510px;top:204px"></div>
    <div class="tile tile--blue" style="left:714px;top:204px"></div>
  </div>
  <div class="partner">
    <div class="partner__name">TQUARLY</div>
    <div class="partner__tagline">KEEPING GYMS IN MOTION</div>
  </div>
  <div class="social">
    <div><span class="social__label">Twitter:</span> @motionLetterbin</div>
    <div><span class="social__label">Facebook:</span> Corvane Motion Limited</div>
  </div>
</section>

</body>
</html>
```